Velmarotix - world unique technology for better life - please let them know who am i at first sight

We need a new business card for company which is a provider of unique crystal based technology suitable for all living being. For more information and final design you can use our brochure (our colours are black and blue from brochure).
We use Verdana font

Industry/Entity Type

Business

Contact Information for Business Card

regular dimension

Font styles to use
Other font styles liked:
• Verdana

Requirements
Must have
• Logo
• name
• function/position
• phone
• mobile
• e-mail
• adress
Nice to have
• inovative design (technology directed)

```html
<!DOCTYPE html>
<html lang="en">
<head>
<meta charset="utf-8">
<title>Velmarotix Business Card</title>
<link href="https://fonts.googleapis.com/css2?family=Open+Sans:wght@300;400;700&display=swap" rel="stylesheet">
<style>
  :root {
    --page-bg: #d9d6d2;
    --card-black: #050505;
    --brand-blue: #1fa3e0;
    --text-grey: #c9c9c9;
    --rule-grey: #3a3a3a;
  }
  * { margin: 0; padding: 0; box-sizing: border-box; }
  html, body {
    width: 1200px; height: 948px; overflow: hidden;
    background: var(--page-bg);
    font-family: "Open Sans", Verdana, sans-serif;
  }
  .sheet {
    width: 1200px; height: 948px;
    display: flex; flex-direction: column; align-items: center; justify-content: center;
    gap: 48px;
  }
  .card {
    width: 700px; height: 400px;
    background: var(--card-black);
    position: relative;
    box-shadow: 0 6px 18px rgba(0,0,0,.25);
  }
  /* front: contact side */
  .card-front { display: flex; }
  .symbol-area {
    width: 330px; height: 100%;
    display: flex; align-items: center; justify-content: center;
  }
  .symbol-disc {
    width: 250px; height: 250px; border-radius: 50%;
    background: radial-gradient(circle at 50% 45%, #4cc3f5 0%, var(--brand-blue) 55%, #0d6fa3 100%);
  }
  .divider {
    width: 1px; height: 300px; align-self: center;
    background: var(--rule-grey);
  }
  .details {
    flex: 1; padding: 56px 0 0 36px; color: var(--text-grey);
  }
  .brand-name {
    font-weight: 300; font-size: 34px; letter-spacing: 3px;
    color: var(--brand-blue); text-transform: uppercase; line-height: 1;
  }
  .person-name {
    margin-top: 34px;
    font-weight: 700; font-size: 24px; color: var(--brand-blue);
  }
  .person-role { font-size: 15px; margin-top: 2px; }
  .contact-list { list-style: none; margin-top: 18px; }
  .contact-list li {
    display: flex; align-items: center; gap: 10px;
    font-size: 14px; line-height: 25px;
  }
  .contact-icon { width: 14px; height: 14px; flex: none; }
  .address { margin-top: 14px; font-size: 14px; line-height: 21px; }
  /* back: brand side */
  .card-back {
    display: flex; flex-direction: column; align-items: center; justify-content: center;
  }
  .brand-lockup { display: flex; align-items: center; gap: 18px; }
  .brand-dot {
    width: 64px; height: 64px; border-radius: 50%;
    background: var(--brand-blue);
  }
  .brand-lockup .brand-name { font-size: 40px; }
  .website {
    margin-top: 30px; font-size: 17px; font-weight: 700;
    letter-spacing: 3px; color: #ffffff;
  }
</style>
</head>
<body>
<main class="sheet">
  <section class="card card-front">
    <div class="symbol-area">
      <div class="symbol-disc" role="img" aria-label="Velmarotix brand symbol area"></div>
    </div>
    <div class="divider"></div>
    <div class="details">
      <p class="brand-name">Velmarotix</p>
      <h1 class="person-name">Mirela Kostanjec</h1>
      <p class="person-role">Founder and CEO</p>
      <ul class="contact-list">
        <li>
          <svg class="contact-icon" viewBox="0 0 14 14"><circle cx="7" cy="7" r="7" fill="var(--brand-blue)"/><path d="M4.5 3.5l1.5 0 .6 2-1 .8a5 5 0 0 0 2.1 2.1l.8-1 2 .6v1.5c-3.5.3-6.3-2.5-6-6z" fill="#000"/></svg>
          014-552-7310
        </li>
        <li>
          <svg class="contact-icon" viewBox="0 0 14 14"><circle cx="7" cy="7" r="7" fill="var(--brand-blue)"/><rect x="5" y="3" width="4" height="8" rx=".8" fill="#000"/></svg>
          014-552-7318
        </li>
        <li>
          <svg class="contact-icon" viewBox="0 0 14 14"><circle cx="7" cy="7" r="7" fill="var(--brand-blue)"/><rect x="3.5" y="4.5" width="7" height="5" fill="#000"/><path d="M3.5 4.5l3.5 3 3.5-3" stroke="var(--brand-blue)" stroke-width=".8" fill="none"/></svg>
          info@velmarotix.com
        </li>
        <li>
          <svg class="contact-icon" viewBox="0 0 14 14"><circle cx="7" cy="7" r="7" fill="var(--brand-blue)"/><circle cx="7" cy="7" r="3.5" fill="none" stroke="#000" stroke-width="1"/><path d="M3.5 7h7M7 3.5v7" stroke="#000" stroke-width=".8"/></svg>
          www.velmarotix.com
        </li>
      </ul>
      <p class="address">Street Name, City Name<br>Zipcode - 01234</p>
    </div>
  </section>

  <section class="card card-back">
    <div class="brand-lockup">
      <div class="brand-dot"></div>
      <p class="brand-name">Velmarotix</p>
    </div>
    <p class="website">www.velmarotix.cu</p>
  </section>
</main>
</body>
</html>
```